Disposable Mini Sauce Pot Design for Asian Chain Food Brands

We operate a Hainan Chicken Rice takeout brand under the name Brindle4U, with our official website: www.Brindle4U.example.
We offer four signature house sauces and are launching brand-new packaging for our sauce line. We require custom graphic designs exclusively for the sauce cup lids.
Product Material & Base Specs
The sauce cups are made of PP plastic, available in two translucent base options: Translucent White and Translucent Orange.
Four Sauce Varieties for Individual Lid Designs
1. Red Sauce – Fried Sweet Chili Sauce
2.Green Sauce – Scallion Oil Dressing
3.Sweet Soy Sauce
4.Sweet Red Sauce (Special for Fried Chicken)
Differentiate each sauce lid design through unique graphics, typography, or illustrative elements for easy customer identification.
The marking NET WT 2 OZ must be clearly printed on every lid.
**There is no need to print full descriptive text or the full name of the sauces on each lid; the design only needs to clearly differentiate the four sauce varieties.
**Please reference the original design style and brand color palette shown on our official website, and feel free to fully unleash your creativity.
Look and feel
Each slider illustrates characteristics of the customer's brand and the style your logo design should communicate.

```html
<!DOCTYPE html>
<html lang="en">
<head>
<meta charset="utf-8">
<title>Brindle4U Sauce Lids</title>
<link rel="stylesheet" href="https://fonts.googleapis.com/css2?family=Montserrat:wght@800;900&display=swap">
<style>
  :root {
    --red: #e30613;
    --green: #6aab2e;
    --blue: #332985;
    --pink: #e63e6d;
    --band: #8b0c22;
    --ink: #ffffff;
    --canvas: #ffffff;
  }
  html, body {
    margin: 0;
    padding: 0;
    width: 1072px;
    height: 1200px;
    overflow: hidden;
    background: var(--canvas);
  }
  .sheet {
    position: relative;
    width: 1072px;
    height: 1200px;
  }
  .lid {
    position: absolute;
    width: 473px;
    height: 537px;
    border-radius: 66px;
    overflow: hidden;
  }
  .lid svg { display: block; width: 473px; height: 537px; }
  .lid--red   { left: 63px;  top: 70px;  background: radial-gradient(circle at 50% 45%, #ee1a1a 0%, var(--red) 70%); }
  .lid--green { left: 558px; top: 70px;  background: radial-gradient(circle at 50% 45%, #74b636 0%, var(--green) 70%); }
  .lid--soy   { left: 63px;  top: 630px; background: radial-gradient(circle at 50% 45%, #3a3090 0%, var(--blue) 70%); }
  .lid--pink  { left: 558px; top: 630px; background: radial-gradient(circle at 50% 45%, #ec4a78 0%, var(--pink) 70%); }

  .headline { font-family: "Montserrat", sans-serif; font-weight: 900; fill: var(--ink); }
  .sauce-word { font-family: "Montserrat", sans-serif; font-weight: 900; fill: var(--ink); }
  .band { fill: var(--band); }
  .net-wt, .variety, .brand-name {
    font-family: "Montserrat", sans-serif;
    font-weight: 900;
    fill: var(--ink);
  }
  .net-wt { font-size: 16px; }
  .variety { font-size: 20px; text-anchor: middle; }
  .brand-name { font-size: 21px; }
</style>
</head>
<body>
<main class="sheet">

  <!-- Red sauce lid -->
  <section class="lid lid--red" aria-label="Red sauce lid">
    <svg viewBox="0 0 473 537" xmlns="http://www.w3.org/2000/svg">
      <text class="headline" x="57" y="340" font-size="397" textLength="247" lengthAdjust="spacingAndGlyphs">R</text>
      <text class="headline" x="312" y="200" font-size="190" textLength="100" lengthAdjust="spacingAndGlyphs">E</text>
      <text class="headline" x="312" y="343" font-size="189" textLength="132" lengthAdjust="spacingAndGlyphs">D</text>
      <text class="sauce-word" x="48" y="421" font-size="132" textLength="386" lengthAdjust="spacingAndGlyphs">sauce</text>
      <path class="band" d="M0 452 C40 444 90 441 140 452 S200 470 237 468 S300 446 340 449 S420 463 473 446 L473 537 L0 537 Z"/>
      <text class="net-wt" x="21" y="493" textLength="100" lengthAdjust="spacingAndGlyphs">NET WT 2 OZ</text>
      <text class="variety" x="237" y="496">FRIED SWEET</text>
      <text class="variety" x="237" y="517">CHILI SAUCE</text>
      <text class="brand-name" x="349" y="494" textLength="106" lengthAdjust="spacingAndGlyphs">Brindle4U</text>
    </svg>
  </section>

  <!-- Green sauce lid -->
  <section class="lid lid--green" aria-label="Green sauce lid">
    <svg viewBox="0 0 473 537" xmlns="http://www.w3.org/2000/svg">
      <text class="headline" x="64" y="231" font-size="255" textLength="179" lengthAdjust="spacingAndGlyphs">G</text>
      <text class="headline" x="255" y="231" font-size="248" textLength="157" lengthAdjust="spacingAndGlyphs">R</text>
      <text class="headline" x="74" y="360" font-size="179" textLength="337" lengthAdjust="spacingAndGlyphs">EEN</text>
      <text class="sauce-word" x="73" y="429" font-size="112" textLength="340" lengthAdjust="spacingAndGlyphs">sauce</text>
      <path class="band" d="M0 452 C40 444 90 441 140 452 S200 470 237 468 S300 446 340 449 S420 463 473 446 L473 537 L0 537 Z"/>
      <text class="net-wt" x="21" y="493" textLength="100" lengthAdjust="spacingAndGlyphs">NET WT 2 OZ</text>
      <text class="variety" x="237" y="496">SCALLION OIL</text>
      <text class="variety" x="237" y="517">DRESSING</text>
      <text class="brand-name" x="349" y="494" textLength="106" lengthAdjust="spacingAndGlyphs">Brindle4U</text>
    </svg>
  </section>

  <!-- Sweet soy sauce lid -->
  <section class="lid lid--soy" aria-label="Sweet soy sauce lid">
    <svg viewBox="0 0 473 537" xmlns="http://www.w3.org/2000/svg">
      <text class="headline" x="73" y="163" font-size="179" textLength="329" lengthAdjust="spacingAndGlyphs">sw</text>
      <text class="headline" x="72" y="288" font-size="216" textLength="324" lengthAdjust="spacingAndGlyphs">eet</text>
      <text class="headline" x="75" y="401" font-size="153" textLength="318" lengthAdjust="spacingAndGlyphs">SOY</text>
      <text class="sauce-word" x="159" y="440" font-size="58" textLength="157" lengthAdjust="spacingAndGlyphs">sauce</text>
      <path class="band" d="M0 449 C40 441 90 438 140 449 S200 467 237 465 S300 443 340 446 S420 460 473 443 L473 537 L0 537 Z"/>
      <text class="net-wt" x="21" y="490" textLength="100" lengthAdjust="spacingAndGlyphs">NET WT 2 OZ</text>
      <text class="brand-name" x="349" y="491" textLength="106" lengthAdjust="spacingAndGlyphs">Brindle4U</text>
    </svg>
  </section>

  <!-- Sweet red sauce lid -->
  <section class="lid lid--pink" aria-label="Sweet red sauce lid">
    <svg viewBox="0 0 473 537" xmlns="http://www.w3.org/2000/svg">
      <text class="headline" x="73" y="163" font-size="179" textLength="329" lengthAdjust="spacingAndGlyphs">sw</text>
      <text class="headline" x="72" y="288" font-size="216" textLength="324" lengthAdjust="spacingAndGlyphs">eet</text>
      <text class="headline" x="86" y="401" font-size="153" textLength="312" lengthAdjust="spacingAndGlyphs">RED</text>
      <text class="sauce-word" x="159" y="440" font-size="58" textLength="158" lengthAdjust="spacingAndGlyphs">sauce</text>
      <path class="band" d="M0 449 C40 441 90 438 140 449 S200 467 237 465 S300 443 340 446 S420 460 473 443 L473 537 L0 537 Z"/>
      <text class="net-wt" x="21" y="490" textLength="100" lengthAdjust="spacingAndGlyphs">NET WT 2 OZ</text>
      <text class="variety" x="237" y="493">SPECIAL FOR</text>
      <text class="variety" x="237" y="514">FRIED CHICKEN</text>
      <text class="brand-name" x="349" y="491" textLength="106" lengthAdjust="spacingAndGlyphs">Brindle4U</text>
    </svg>
  </section>

</main>
</body>
</html>
```